Business Card Design Project

Looking to update our business cards. We have a logo with our slogan. We are an IT firm so we wouldlike a modern look.

Industry/Entity Type

Business

```html
<!DOCTYPE html>
<html lang="en">
<head>
<meta charset="UTF-8">
<title>Nexloop Business Card Set</title>
<link href="https://fonts.googleapis.com/css2?family=Jost:wght@400;500;600&family=Source+Sans+3:wght@400&display=swap" rel="stylesheet">
<style>
  :root {
    --stage: #8a5a36;
    --label: #1f1208;
    --card-white: #ffffff;
    --charcoal: #3a3a3a;
    --brand-green: #5f7d32;
    --accent-green: #a9c441;
    --lime: #b1c244;
    --ink: #1e1e1e;
    --on-dark: #ffffff;
  }
  html, body {
    margin: 0;
    padding: 0;
    overflow: hidden;
  }
  body {
    width: 1200px;
    height: 788px;
    background: var(--stage);
    position: relative;
    font-family: "Jost", "Futura", sans-serif;
  }
  .view-label {
    position: absolute;
    width: 200px;
    margin-left: -100px;
    text-align: center;
    font-family: "Source Sans 3", "Myriad Pro", sans-serif;
    font-size: 21px;
    color: var(--label);
  }
  .card {
    position: absolute;
    width: 526px;
    height: 299px;
    border-radius: 22px;
    overflow: hidden;
  }
  .card--front { left: 52px; top: 80px; background: var(--card-white); }
  .card--plain { left: 620px; top: 80px; background: var(--card-white); }
  .card--lime { left: 49px; top: 455px; background: var(--lime); }
  .card--visual { left: 621px; top: 455px; }

  .front-band {
    position: absolute;
    left: 0; right: 0;
    top: 30px; height: 240px;
    background: var(--charcoal);
  }

  /* Brand lockup */
  .brand {
    position: absolute;
    text-align: center;
  }
  .brand__row {
    display: flex;
    align-items: center;
    justify-content: center;
    gap: 10px;
  }
  .brand__dot {
    border-radius: 50%;
    background: var(--brand-green);
  }
  .brand__name {
    font-weight: 500;
    color: var(--brand-green);
    letter-spacing: 0.08em;
    line-height: 1;
  }
  .brand__tagline {
    font-weight: 600;
    color: var(--ink);
    letter-spacing: 0.25em;
    white-space: nowrap;
    line-height: 16px;
  }
  .brand--large { left: 0; right: 0; top: 112px; }
  .brand--large .brand__name { font-size: 50px; }
  .brand--large .brand__dot { width: 16px; height: 16px; }
  .brand--large .brand__tagline { font-size: 14px; margin-top: 2px; }

  .brand--small { left: 28px; width: 240px; top: 100px; }
  .brand--small .brand__name { font-size: 30px; }
  .brand--small .brand__dot { width: 10px; height: 10px; }
  .brand--small .brand__tagline { font-size: 9.5px; margin-top: 4px; color: var(--on-dark); letter-spacing: 0.2em; line-height: 12px; }

  .front-divider {
    position: absolute;
    left: 275px;
    top: 20px;
    width: 1px;
    height: 196px;
    background: var(--accent-green);
  }
  .contact {
    position: absolute;
    left: 290px;
    top: 24px;
    color: var(--on-dark);
    font-size: 13.5px;
    line-height: 20px;
  }
  .contact__name {
    font-size: 18px;
    font-weight: 600;
    color: var(--accent-green);
    line-height: 22px;
  }
  .contact__role {
    font-size: 13.5px;
    color: var(--accent-green);
    margin-bottom: 7px;
  }
  .contact__phones { margin-bottom: 14px; }
  .contact__web { margin-bottom: 11px; }
  .contact__key { font-weight: 600; font-style: italic; }

  .visual-fill {
    position: absolute;
    inset: 0;
    background: radial-gradient(ellipse at 55% 50%, #f4f8ff 0%, #b9d4f5 22%, #4a7fd0 50%, #1d3f9a 75%, #0e1f5a 100%);
  }
</style>
</head>
<body>
  <div class="view-label" style="left:320px; top:33px;">Front</div>
  <div class="view-label" style="left:896px; top:33px;">Back - 1</div>
  <div class="view-label" style="left:310px; top:404px;">Back - 2</div>
  <div class="view-label" style="left:896px; top:404px;">Back - 3</div>

  <section class="card card--front">
    <div class="front-band">
      <div class="brand brand--small">
        <div class="brand__row"><span class="brand__name">NEXLOOP</span><span class="brand__dot"></span></div>
        <div class="brand__tagline">SMART SYSTEMS MADE EASY</div>
      </div>
      <div class="front-divider"></div>
      <div class="contact">
        <div class="contact__name">Your Name</div>
        <div class="contact__role">Designation</div>
        <div class="contact__phones">
          <div><span class="contact__key">p</span> : +12 345 67890</div>
          <div><span class="contact__key">f</span> : +12 345 67890</div>
        </div>
        <div class="contact__web">
          <div><span class="contact__key">e</span> : info@website.com</div>
          <div><span class="contact__key">w</span> : www.website.com</div>
        </div>
        <div>#0000, Street Name</div>
        <div>Area Name, Country</div>
      </div>
    </div>
  </section>

  <section class="card card--plain">
    <div class="brand brand--large">
      <div class="brand__row"><span class="brand__name">NEXLOOP</span><span class="brand__dot"></span></div>
      <div class="brand__tagline">SMART SYSTEMS MADE EASY</div>
    </div>
  </section>

  <section class="card card--lime">
    <div class="brand brand--large">
      <div class="brand__row"><span class="brand__name">NEXLOOP</span><span class="brand__dot"></span></div>
      <div class="brand__tagline">SMART SYSTEMS MADE EASY</div>
    </div>
  </section>

  <section class="card card--visual">
    <div class="visual-fill" role="img" aria-label="Abstract blue technology backdrop with glowing light burst, grid lines and binary digits"></div>
    <div class="brand brand--large">
      <div class="brand__row"><span class="brand__name">NEXLOOP</span><span class="brand__dot"></span></div>
      <div class="brand__tagline">SMART SYSTEMS MADE EASY</div>
    </div>
  </section>
</body>
</html>
```